Puffy Clouds Cotton Candy

Looking for a logo design and business cards to help a 13 year old entrepreneur promote her cotton candy business.
Contact Information for Business Card
Name, Phone & Email
Colors
E54698
E96AAD
F1A4CE
F9D9EA
FCEFF6
A7469A
B969AE
D3A5CF
EDDBEB
F8F0F9
6B429C
8869AF
B7A5CE
E3DAEB
F3F0F8
Requirements
Must have
- A fun feel that is appropriate for a teenage girl selling cotton candy

```html
<!DOCTYPE html>
<html lang="en">
<head>
<meta charset="utf-8">
<title>Puffy Clouds Cotton Candy – Business Card</title>
<link rel="stylesheet" href="https://fonts.googleapis.com/css2?family=Poppins:wght@600;700&family=Lato:wght@400&display=swap">
<style>
  :root {
    --bg: #1f1f1f;
    --pink: #E54698;
    --pink-soft: #E96AAD;
    --purple: #6B429C;
    --purple-mid: #8869AF;
    --white: #ffffff;
  }
  * { box-sizing: border-box; margin: 0; padding: 0; }
  html, body { width: 1200px; height: 1015px; overflow: hidden; background: var(--bg); }
  .canvas {
    width: 1200px; height: 1015px;
    display: flex; flex-direction: column; align-items: center; justify-content: center; gap: 45px;
  }
  .card {
    position: relative; width: 770px; height: 440px; overflow: hidden;
    box-shadow: 0 12px 30px rgba(0,0,0,.55);
  }
  /* Front */
  .card--front {
    background: radial-gradient(ellipse 60% 75% at 50% 48%, var(--pink) 0%, #B5469E 40%, var(--purple) 85%);
    display: flex; flex-direction: column; align-items: center; justify-content: center; gap: 22px;
  }
  .brand-dot { width: 120px; height: 120px; border-radius: 50%; border: 6px solid var(--white); }
  .brand-name {
    font-family: "Poppins", sans-serif; font-weight: 700; text-align: center;
    line-height: 1.05; letter-spacing: .5px;
  }
  .card--front .brand-name { color: var(--white); font-size: 46px; }
  .brand-name .sub { display: block; font-size: .7em; }
  /* Back */
  .card--back { background: var(--purple); }
  .card__art { position: absolute; inset: 0; }
  .contact { position: absolute; left: 60px; top: 120px; color: var(--white); }
  .contact__name { font-family: "Poppins", sans-serif; font-weight: 700; font-size: 32px; letter-spacing: 1px; }
  .contact__role { font-family: "Lato", sans-serif; font-size: 19px; margin-top: 2px; }
  .contact__address, .contact__lines { font-family: "Lato", sans-serif; font-size: 20px; line-height: 1.3; }
  .contact__address { margin-top: 52px; }
  .contact__lines { margin-top: 48px; list-style: none; }
  .contact__lines li { display: flex; align-items: center; gap: 10px; }
  .contact__lines svg { width: 20px; height: 20px; fill: var(--white); }
  .back-brand {
    position: absolute; left: 470px; top: 60px; width: 270px;
    display: flex; flex-direction: column; align-items: center; gap: 18px;
  }
  .back-brand .brand-dot { border-color: var(--pink); width: 110px; height: 110px; }
  .back-brand .brand-name { color: var(--pink); font-size: 38px; }
</style>
</head>
<body>
<main class="canvas">
  <section class="card card--front">
    <span class="brand-dot" aria-hidden="true"></span>
    <h1 class="brand-name">Puffy Clouds<span class="sub">Cotton Candy</span></h1>
  </section>

  <section class="card card--back">
    <svg class="card__art" viewBox="0 0 770 440" aria-hidden="true">
      <circle cx="610" cy="190" r="280" fill="var(--white)"/>
      <path d="M400 60 A250 250 0 0 0 620 440" fill="none" stroke="var(--pink)" stroke-width="5"/>
    </svg>
    <div class="contact">
      <h2 class="contact__name">Maya Lawson</h2>
      <p class="contact__role">Managing Director</p>
      <p class="contact__address">88 Maple Lane<br>Springfield, 45210</p>
      <ul class="contact__lines">
        <li><svg viewBox="0 0 24 24"><path d="M6.6 10.8a15.1 15.1 0 0 0 6.6 6.6l2.2-2.2a1 1 0 0 1 1-.25 11.4 11.4 0 0 0 3.6.57 1 1 0 0 1 1 1V20a1 1 0 0 1-1 1A17 17 0 0 1 3 4a1 1 0 0 1 1-1h3.5a1 1 0 0 1 1 1c0 1.25.2 2.45.57 3.57a1 1 0 0 1-.25 1z"/></svg>044-987 654 321</li>
        <li><svg viewBox="0 0 24 24"><path d="M2 5h20v14H2zm2 2v.5l8 5 8-5V7l-8 5z"/></svg>hello@puffyclouds.com</li>
      </ul>
    </div>
    <div class="back-brand">
      <span class="brand-dot" aria-hidden="true"></span>
      <p class="brand-name">Puffy Clouds<span class="sub">Cotton Candy</span></p>
    </div>
  </section>
</main>
</body>
</html>
```